Business Card Design

Business Card for professional consulting firm working with large financial institutions.

Target Market(s)

Executive buyers

Industry/Entity Type

Banking

Contact Information for Business Card

Mild creativity wanted. Not boring, but do elaborate artwork.

Font styles to use
Serif
Sans Serif

Colors

Designer to choose colors to be used in the design.

Requirements
Must have
• Standard business card features - company name, individual name, telephone, website, email, locations.
Nice to have
• Two colors
Should not have
• too many colors, fancy printing, cartoons.

```html
<!DOCTYPE html>
<html lang="en">
<head>
<meta charset="utf-8">
<title>Northvale Business Card</title>
<link rel="stylesheet" href="https://fonts.googleapis.com/css2?family=Merriweather:wght@400&family=Roboto:wght@400;500;700&display=swap">
<style>
  :root {
    --backdrop: #e8e5e0;
    --card-light: #f3f3f3;
    --card-dark: #1c1d1f;
    --accent-bar: #0b0b0b;
    --ink: #111111;
    --ink-soft: #555555;
    --ink-muted: #a9a9a9;
    --paper-white: #ffffff;
  }
  * { margin: 0; padding: 0; box-sizing: border-box; }
  html, body {
    width: 1200px;
    height: 960px;
    overflow: hidden;
    background: var(--backdrop);
  }
  .canvas {
    position: relative;
    width: 1200px;
    height: 960px;
  }
  .card {
    position: absolute;
    box-shadow: 0 2px 6px rgba(0,0,0,0.25);
  }
  .card-front {
    left: 313px; top: 113px;
    width: 602px; height: 344px;
    background: var(--card-light);
  }
  .accent-bar {
    position: absolute;
    left: 0; top: 0;
    width: 14px; height: 100%;
    background: var(--accent-bar);
  }
  .brand-name {
    position: absolute;
    font-family: "Merriweather", Georgia, serif;
    font-weight: 400;
    white-space: nowrap;
  }
  .card-front .brand-name {
    left: 84px; top: 56px;
    font-size: 29px;
    color: var(--ink);
  }
  .contact-block {
    position: absolute;
    left: 38px; top: 182px;
    font-family: "Roboto", Arial, sans-serif;
    font-size: 14.5px;
    line-height: 18px;
    color: var(--ink-soft);
  }
  .contact-list {
    list-style: none;
    margin-top: 9px;
  }
  .contact-list li {
    display: flex;
    align-items: center;
    gap: 7px;
    height: 19.5px;
  }
  .contact-list svg {
    width: 13px; height: 13px;
    fill: var(--ink);
    flex: none;
  }
  .person {
    position: absolute;
    left: 398px; top: 221px;
    width: 130px;
    text-align: center;
    font-family: "Roboto", Arial, sans-serif;
  }
  .person-name {
    font-size: 22px;
    font-weight: 500;
    color: var(--ink);
    letter-spacing: 0.2px;
    white-space: nowrap;
  }
  .person-title {
    font-size: 14px;
    font-weight: 500;
    color: var(--ink-muted);
    margin-top: 1px;
  }
  .card-back {
    left: 311px; top: 472px;
    width: 601px; height: 343px;
    background: var(--card-dark);
  }
  .card-back .brand-name {
    left: 0; right: 0; top: 145px;
    text-align: center;
    font-size: 34px;
    color: var(--paper-white);
  }
  .back-url {
    position: absolute;
    left: 0; right: 0; top: 280px;
    text-align: center;
    font-family: "Roboto", Arial, sans-serif;
    font-size: 13.5px;
    letter-spacing: 5.4px;
    color: var(--paper-white);
  }
</style>
</head>
<body>
<main class="canvas">
  <section class="card card-front">
    <div class="accent-bar"></div>
    <div class="brand-name">Northvale</div>

    <address class="contact-block" style="font-style: normal;">
      <div>Northvale</div>
      <div>4120 Harbor Ridge Road</div>
      <div>Juneau, Alaska 99801</div>
      <ul class="contact-list">
        <li>
          <svg viewBox="0 0 24 24" aria-hidden="true"><path d="M6.6 10.8c1.4 2.8 3.8 5.1 6.6 6.6l2.2-2.2c.3-.3.7-.4 1-.2 1.1.4 2.3.6 3.6.6.6 0 1 .4 1 1V20c0 .6-.4 1-1 1C10.6 21 3 13.4 3 4c0-.6.4-1 1-1h3.5c.6 0 1 .4 1 1 0 1.3.2 2.5.6 3.6.1.3 0 .7-.2 1l-2.3 2.2z"/></svg>
          <span>555 210 4837</span>
        </li>
        <li>
          <svg viewBox="0 0 24 24" aria-hidden="true"><path d="M2 5h20v2l-10 6L2 7z"/><path d="M2 9l10 6 10-6v10H2z"/></svg>
          <span>info@northvale.com</span>
        </li>
        <li>
          <svg viewBox="0 0 24 24" aria-hidden="true"><path d="M12 2a10 10 0 1 0 0 20 10 10 0 0 0 0-20zm-1 17.9A8 8 0 0 1 4.2 10l4.8 4.8v1c0 1.1.9 2 2 2zm6.9-2.5c-.3-.8-1-1.4-1.9-1.4h-1v-3c0-.6-.4-1-1-1H8v-2h2c.6 0 1-.4 1-1V7h2c1.1 0 2-.9 2-2v-.4a8 8 0 0 1 2.9 12.8z"/></svg>
          <span>www.northvale.com</span>
        </li>
      </ul>
    </address>

    <div class="person">
      <div class="person-name">DANIEL REEVE</div>
      <div class="person-title">CEO/FOUNDER</div>
    </div>
  </section>

  <section class="card card-back">
    <div class="brand-name">Northvale</div>
    <div class="back-url">www.northvale.com</div>
  </section>
</main>
</body>
</html>
```